business card - Helicopter Flight Services, Flight School, etc.

We need a business card design for a new helicopter service.

We offer Helicopter Flight Services, Aerial Filming & Photography, Flight School, and Helicopter Tours. In that order.

Summit BladeAir, Inc.
Dennis Tollerby
SummitBladeair@Kestmail.com
626-418-7352

Based at the Brenwick Airport in Van Nuys, CA. The final design should communicate integrity and safety. Pictures or logos at your discretion.

Card back side - surprise me.

```html
<!DOCTYPE html>
<html lang="en">
<head>
<meta charset="utf-8">
<title>Summit BladeAir, Inc. – Business Card</title>
<link rel="stylesheet" href="https://fonts.googleapis.com/css2?family=Noto+Sans:wght@400;500&family=Noto+Serif:wght@700&display=swap">
<style>
  :root {
    --page-bg: #ecebe8;
    --card-bg: #ffffff;
    --ink: #111111;
    --band-blue: #7ba3d8;
    --rule-blue: #7aa0d4;
    --swoosh-grey: #4d4d4d;
    --art-warm: #d9c9a0;
    --art-cool: #c9d3dc;
    --ghost: #e6ecf1;
  }
  html, body {
    margin: 0;
    width: 1189px;
    height: 1200px;
    overflow: hidden;
    background: var(--page-bg);
  }
  .sheet { display: block; width: 1189px; height: 1200px; }
  .card { fill: var(--card-bg); }
  .card-shadow { fill: rgba(0,0,0,0.18); }
  .brand-sans { font-family: "Noto Sans", sans-serif; font-weight: 500; fill: var(--ink); }
  .brand-serif { font-family: "Noto Serif", serif; font-weight: 700; fill: var(--ink); }
  .person-name { font-family: "Noto Serif", serif; font-weight: 700; fill: var(--ink); }
  .contact, .address, .service { font-family: "Noto Sans", sans-serif; font-weight: 500; fill: var(--ink); }
  .divider { stroke: var(--rule-blue); stroke-width: 2.5; }
  .band { fill: var(--band-blue); }
  .swoosh { fill: none; stroke: var(--swoosh-grey); stroke-width: 6; }
  .icon { fill: var(--ink); }
  .icon-line { fill: none; stroke: #fff; stroke-width: 1.4; }
  .bullet { stroke: var(--ink); stroke-width: 2; stroke-linecap: round; }
</style>
</head>
<body>
<svg class="sheet" viewBox="0 0 1189 1200" xmlns="http://www.w3.org/2000/svg">
  <defs>
    <linearGradient id="art-fill" x1="0" y1="0" x2="1" y2="1">
      <stop offset="0" stop-color="#d9c9a0"/>
      <stop offset="1" stop-color="#c9d3dc"/>
    </linearGradient>
    <radialGradient id="ghost-fill" cx="0.5" cy="0.5" r="0.6">
      <stop offset="0" stop-color="#e6ecf1"/>
      <stop offset="1" stop-color="#ffffff"/>
    </radialGradient>
    <clipPath id="front-clip"><rect width="917" height="522"/></clipPath>
    <clipPath id="swoosh-clip">
      <rect x="0" y="0" width="370" height="522"/>
      <rect x="580" y="0" width="337" height="522"/>
    </clipPath>
  </defs>

  <!-- Front of card -->
  <g class="card-front" transform="translate(140 45)">
    <rect class="card-shadow" x="4" y="5" width="917" height="522"/>
    <rect class="card" width="917" height="522"/>
    <g clip-path="url(#front-clip)">
      <text class="brand-sans" x="458" y="96" font-size="68" text-anchor="middle">Summit BladeAir, Inc.</text>

      <rect x="43" y="141" width="323" height="239" rx="18" fill="url(#art-fill)" role="img" aria-label="Illustration of two smiling tour guides beside a control tower and a jet on a runway"/>

      <line class="divider" x1="423" y1="128" x2="423" y2="361"/>

      <text class="person-name" x="463" y="228" font-size="36">Dennis Tollerby</text>

      <g class="icon-phone" transform="translate(465 280)">
        <rect class="icon" width="20" height="20"/>
        <path d="M6 4 q-3 6 2 12 l3 -2 -2 -3 -1 1 q-1 -3 0 -5 l1 1 2 -2 z" fill="#fff"/>
      </g>
      <text class="contact" x="502" y="298" font-size="25">626-418-7352</text>

      <g class="icon-mail" transform="translate(465 316)">
        <rect class="icon" width="20" height="15"/>
        <path class="icon-line" d="M1 1 L10 9 L19 1 M1 14 L8 7 M19 14 L12 7"/>
      </g>
      <text class="contact" x="502" y="332" font-size="25">SummitBladeair@Kestmail.com</text>

      <path class="band" d="M0 440 Q458 310 917 428 L917 522 L0 522 Z"/>
      <path class="swoosh" clip-path="url(#swoosh-clip)" d="M0 452 Q458 325 917 440"/>

      <text class="address" x="444" y="476" font-size="26" text-anchor="middle">2840 W. Larkspur Ave. Ste.B  Van Nuys, CA 91406</text>
    </g>
  </g>

  <!-- Back of card -->
  <g class="card-back" transform="translate(140 623)">
    <rect class="card-shadow" x="4" y="5" width="917" height="522"/>
    <rect class="card" width="917" height="522"/>

    <rect x="18" y="95" width="875" height="375" rx="180" fill="url(#ghost-fill)" role="img" aria-label="Faint watermark illustration of a helicopter among clouds"/>

    <text class="brand-serif" x="458" y="186" font-size="56" text-anchor="middle">Summit BladeAir, Inc.</text>

    <g class="services" font-size="25">
      <path class="bullet" transform="translate(62 248)" d="M-8 0 H8 M0 -8 V8 M-6 -6 L6 6 M-6 6 L6 -6"/>
      <text class="service" x="80" y="257">Helicopter Flight Services</text>

      <path class="bullet" transform="translate(482 248)" d="M-8 0 H8 M0 -8 V8 M-6 -6 L6 6 M-6 6 L6 -6"/>
      <text class="service" x="500" y="257">Aerial Filming &amp; Photography</text>

      <path class="bullet" transform="translate(62 296)" d="M-8 0 H8 M0 -8 V8 M-6 -6 L6 6 M-6 6 L6 -6"/>
      <text class="service" x="80" y="305">Flight School</text>

      <path class="bullet" transform="translate(482 296)" d="M-8 0 H8 M0 -8 V8 M-6 -6 L6 6 M-6 6 L6 -6"/>
      <text class="service" x="500" y="305">Helicopter Tours</text>
    </g>
  </g>
</svg>
</body>
</html>
```